Business card design for Nerith Engineering Tandem

We need a new business card design along with all the necessary to place an order. The company is Nerith Engineering Tandem and we recently updated our logo.

```html
<!DOCTYPE html>
<html lang="en">
<head>
<meta charset="utf-8">
<title>Nerith Engineering Tandem – Business Card</title>
<link rel="stylesheet" href="https://fonts.googleapis.com/css2?family=Montserrat:wght@400;500;700;800&display=swap">
<style>
  :root {
    --bg: #3b3c3d;
    --card-white: #f1f1f1;
    --gold: #d8b61a;
    --logo-grey: #7b7b7b;
    --ink: #222222;
    --white: #ffffff;
  }
  * { margin: 0; padding: 0; box-sizing: border-box; }
  html, body {
    width: 1200px;
    height: 1059px;
    overflow: hidden;
    background: var(--bg);
    font-family: "Montserrat", sans-serif;
  }
  .canvas { position: relative; width: 1200px; height: 1059px; }

  .card {
    position: absolute;
    border-radius: 24px;
    overflow: hidden;
  }
  .card--front { left: 256px; top: 100px; width: 688px; height: 393px; background: var(--card-white); }
  .card--back  { left: 253px; top: 536px; width: 694px; height: 396px; background: var(--gold); }

  /* brand lockup (name set as text) */
  .brand {
    position: absolute;
    display: flex;
    align-items: center;
  }
  .brand__mark { flex: none; }
  .brand__name {
    font-weight: 700;
    line-height: 1;
    text-transform: uppercase;
  }
  .brand__primary { display: block; }
  .brand__secondary { display: block; letter-spacing: 0.04em; }

  .card--front .brand { left: 59px; top: 166px; gap: 16px; }
  .card--front .brand__mark { width: 58px; height: 58px; background: var(--gold); }
  .card--front .brand__name { color: var(--logo-grey); }
  .card--front .brand__primary { font-size: 46px; }
  .card--front .brand__secondary { font-size: 14px; margin-top: 6px; }

  .card--back .brand { left: 71px; top: 132px; gap: 32px; }
  .card--back .brand__mark { width: 128px; height: 128px; background: var(--white); }
  .card--back .brand__name { color: var(--white); }
  .card--back .brand__primary { font-size: 94px; }
  .card--back .brand__secondary { font-size: 30px; margin-top: 10px; }

  /* contact column */
  .divider {
    position: absolute;
    left: 367px;
    top: 90px;
    width: 2px;
    height: 213px;
    background: var(--gold);
  }
  .contact {
    position: absolute;
    left: 394px;
    top: 86px;
    color: var(--ink);
  }
  .contact__name {
    font-weight: 800;
    font-size: 30px;
    color: var(--gold);
    letter-spacing: 0.02em;
    line-height: 1;
  }
  .contact__role {
    font-size: 18.5px;
    font-weight: 500;
    margin-top: 6px;
  }
  .contact__address {
    font-size: 18.5px;
    font-weight: 500;
    line-height: 27.5px;
    margin-top: 12px;
    font-style: normal;
  }
  .contact__list { list-style: none; margin-top: 12px; }
  .contact__item {
    display: flex;
    align-items: center;
    gap: 8px;
    font-size: 18.5px;
    font-weight: 500;
    height: 27.5px;
  }
  .contact__icon { width: 15px; height: 15px; flex: none; fill: var(--gold); }
</style>
</head>
<body>
<main class="canvas">

  <section class="card card--front" aria-label="Business card front">
    <div class="brand">
      <span class="brand__mark"></span>
      <span class="brand__name">
        <span class="brand__primary">Nerith</span>
        <span class="brand__secondary">Engineering Tandem</span>
      </span>
    </div>

    <div class="divider"></div>

    <div class="contact">
      <h1 class="contact__name">DANIEL REYES</h1>
      <p class="contact__role">Managing Director</p>
      <address class="contact__address">Your address, City<br>State, Zip 1234</address>
      <ul class="contact__list">
        <li class="contact__item">
          <svg class="contact__icon" viewBox="0 0 16 16" aria-hidden="true">
            <path d="M1 5c0-2 3-3 7-3s7 1 7 3v1.5h-3.5V5H4.5v1.5H1z"/>
            <path d="M4 7.5h8l2 6.5H2z"/>
          </svg>
          123 456 789
        </li>
        <li class="contact__item">
          <svg class="contact__icon" viewBox="0 0 16 16" aria-hidden="true">
            <path d="M1 3.5h14v1L8 9 1 4.5z"/>
            <path d="M1 6l7 4.5L15 6v6.5H1z"/>
          </svg>
          info@yourgmail.com
        </li>
        <li class="contact__item">
          <svg class="contact__icon" viewBox="0 0 16 16" aria-hidden="true">
            <circle cx="8" cy="8" r="7"/>
          </svg>
          www.yourwebsite.com
        </li>
      </ul>
    </div>
  </section>

  <section class="card card--back" aria-label="Business card back">
    <div class="brand">
      <span class="brand__mark"></span>
      <span class="brand__name">
        <span class="brand__primary">Nerith</span>
        <span class="brand__secondary">Engineering Tandem</span>
      </span>
    </div>
  </section>

</main>
</body>
</html>
```